Rebrand stationary with recently completed logo design

Need new business cards, thank you cards, letterhead, envelopes and presentation folders. The designs will be sent to a separate production firm so I need the files to be print ready.

My contact info
Reko Haliburn

Office 604-318-5047
Fax 604-371-8054

Email reko@glazemark.ca
website www.glazemark.ca

315-14720 62nd Avenue,
Langley, BC, V2K 3R8

Target Market(s)

Homeowners, businesses and contractors

Industry/Entity Type

Business

Font styles to use
Sans Serif

Colors
34a7d7

Requirements
Must have
• Like to have one side of the business card a solid color with the logo in all white. The side with all the text to be a white background
• I find the current blue on the front of the card with the white logo too dark.
Should not have
• Gradient colors

```html
<!DOCTYPE html>
<html lang="en">
<head>
<meta charset="utf-8">
<title>Glazemark Business Card</title>
<link rel="stylesheet" href="https://fonts.googleapis.com/css2?family=Source+Sans+3:wght@400;600&display=swap">
<style>
  :root {
    --brand-blue: #34a7d7;
    --slate: #3e4c56;
    --card-white: #f4f4f3;
    --text-grey: #5a5d60;
    --backdrop: #d8d5d1;
  }
  * { margin: 0; padding: 0; box-sizing: border-box; }
  html, body {
    width: 1200px; height: 960px; overflow: hidden;
    background: var(--backdrop);
    font-family: "Source Sans 3", sans-serif;
  }
  .card {
    position: absolute;
    width: 600px; height: 342px;
    box-shadow: 0 2px 6px rgba(0,0,0,0.25);
    overflow: hidden;
  }
  .card--front { left: 302px; top: 130px; background: var(--card-white); }
  .card--back { left: 299px; top: 490px; width: 601px; height: 340px; background: var(--slate); }

  .front-panel { position: absolute; inset: 0; }

  .wordmark {
    position: absolute; left: 39px; top: 56px;
    font-size: 42px; font-weight: 400; letter-spacing: 0.5px;
    color: var(--brand-blue); line-height: 1;
  }
  .holder-name {
    position: absolute; left: 42px; top: 130px;
    font-size: 19px; font-weight: 600; color: var(--brand-blue);
    letter-spacing: 0.3px; text-transform: uppercase;
  }
  .address {
    position: absolute; left: 44px; top: 162px;
    font-size: 14px; line-height: 19px; color: var(--text-grey);
  }
  .contact-list {
    position: absolute; left: 44px; top: 210px;
    list-style: none; font-size: 14px; line-height: 19px; color: var(--text-grey);
  }
  .contact-list li { display: flex; align-items: center; gap: 9px; }
  .contact-list svg { width: 13px; height: 13px; fill: var(--brand-blue); flex: none; }

  .back-lockup {
    position: absolute; left: 125px; top: 107px;
    display: flex; align-items: center; gap: 16px;
  }
  .back-lockup .mark-square {
    width: 58px; height: 58px; background: #ffffff;
  }
  .back-lockup .wordmark-back {
    font-size: 50px; font-weight: 400; color: #ffffff; line-height: 1; letter-spacing: 0.5px;
  }
</style>
</head>
<body>
  <section class="card card--front">
    <svg class="front-panel" width="600" height="342" viewBox="0 0 600 342">
      <polygon points="403,0 600,0 600,342 440,342" fill="var(--slate)"/>
    </svg>
    <div class="wordmark">GLAZEMARK</div>
    <div class="holder-name">Reko Haliburn</div>
    <p class="address">315-14720 62nd Avenue<br>Langley, BC, V2K 3R8</p>
    <ul class="contact-list">
      <li><svg viewBox="0 0 16 16"><path d="M3.5 1l2.5 3-1.5 2c.8 1.8 2.2 3.2 4 4l2-1.5 3 2.5-1.5 2.5C6.5 13.5 2.5 9.5 1 3.5z"/></svg>604-318-5047</li>
      <li><svg viewBox="0 0 16 16"><rect x="4" y="1" width="8" height="4"/><rect x="1" y="6" width="14" height="6" rx="1"/><rect x="4" y="10" width="8" height="5"/></svg>604-371-8054</li>
      <li><svg viewBox="0 0 16 16"><path d="M1 3h14v1.5L8 9 1 4.5z"/><path d="M1 6l7 4.5L15 6v7H1z"/></svg>reko@glazemark.ca</li>
      <li><svg viewBox="0 0 16 16"><circle cx="8" cy="8" r="7"/></svg>www.glazemark.ca</li>
    </ul>
  </section>

  <section class="card card--back">
    <div class="back-lockup">
      <div class="mark-square"></div>
      <div class="wordmark-back">GLAZEMARK</div>
    </div>
  </section>
</body>
</html>
```